2021 Summer Ads Hollis Bay Custom Homes

We need a re-design of our summer ad run for our customer, Hollis Bay Custom Homes. They are custom home builders in the mostly rural parts of West Virginia, USA. They are known for their "Forever Home" tagline. We'd like two designed ads with the main difference being just the custom home that's featured. These designs should be for a Zintrola banner like 300 x 250 and square ad like 250 x 250. For inspiration please visit the Hollis Bay Custom Homes website at www dot hollisbaycustomhomes dot com

Target Market(s)

consumers / new home shoppers

Industry/Entity Type

Consumer

Requirements
Must have
• HBCH logo
Price Lock Available!
Custom home pic
Learn more >
small CFRM logo mark

```html
<!DOCTYPE html>
<html lang="en">
<head>
<meta charset="utf-8">
<title>Hollis Bay Custom Homes – Summer Ads</title>
<link rel="stylesheet" href="https://fonts.googleapis.com/css2?family=Lora:wght@600;700&family=Roboto:wght@400&display=swap">
<style>
  :root {
    --canvas: #dedede;
    --navy: #1c2535;
    --navy-mid: #3a2433;
    --red: #b3111b;
    --red-deep: #8e0c14;
    --red-bright: #d0121c;
    --white: #ffffff;
    --grass: #5e7a3e;
  }
  * { margin: 0; padding: 0; box-sizing: border-box; }
  html, body { width: 1200px; height: 609px; overflow: hidden; }
  body {
    background: var(--canvas);
    position: relative;
    font-family: "Roboto", Arial, sans-serif;
  }
  .ad {
    position: absolute;
    top: 22px;
    height: 504px;
    overflow: hidden;
    background: linear-gradient(90deg, var(--navy) 0%, var(--navy-mid) 38%, var(--red) 72%);
    box-shadow: 0 2px 8px rgba(0,0,0,.35);
  }
  .ad--banner { left: 26px; width: 605px; }
  .ad--square { left: 662px; width: 504px; }

  .ad__photo { position: absolute; inset: 0; }
  .ad--banner .ad__photo {
    clip-path: polygon(397px 0, 100% 0, 100% 100%, 286px 100%);
    background: linear-gradient(180deg, #6f9fd2 0%, #d9dfe3 30%, #e9eaea 55%, #3d3d40 75%, var(--grass) 100%);
  }
  .ad--square .ad__photo {
    clip-path: polygon(383px 0, 100% 0, 100% 100%, 290px 100%);
    background: linear-gradient(180deg, #b8d2ee 0%, #4f7a3a 30%, #9c2a1c 55%, #a8331f 72%, #c9c2b2 100%);
  }
  .ad__edge { position: absolute; inset: 0; width: 100%; height: 100%; }

  .brand {
    position: absolute;
    left: 32px;
    top: 32px;
    display: flex;
    align-items: center;
    gap: 10px;
  }
  .brand__mark { width: 22px; height: 22px; background: var(--white); }
  .brand__name {
    font-family: "Lora", Georgia, serif;
    font-weight: 600;
    font-size: 26px;
    letter-spacing: 1px;
    color: var(--white);
    text-transform: uppercase;
    line-height: 1.05;
  }
  .badge {
    position: absolute;
    top: 25px;
    width: 54px;
    height: 54px;
    border-radius: 50%;
    background: var(--white);
  }
  .ad--banner .badge { right: 31px; }
  .ad--square .badge { right: 17px; }

  .ad__title {
    position: absolute;
    left: 34px;
    top: 166px;
    font-family: "Lora", Georgia, serif;
    font-weight: 700;
    font-size: 50px;
    line-height: 1.2;
    color: var(--white);
    letter-spacing: 1px;
  }
  .ad__copy {
    position: absolute;
    left: 34px;
    top: 322px;
    width: 230px;
    font-size: 16.5px;
    line-height: 1.95;
    color: var(--white);
  }
  .ad__cta {
    position: absolute;
    left: 34px;
    top: 442px;
    display: flex;
    align-items: center;
    gap: 8px;
    font-family: "Lora", Georgia, serif;
    font-weight: 700;
    font-size: 15px;
    color: var(--white);
    text-decoration: none;
    letter-spacing: .5px;
  }
  .ad__cta svg { width: 16px; height: 16px; }

  .price-lock {
    position: absolute;
    top: 388px;
    width: 108px;
    height: 108px;
    border-radius: 50%;
    background: var(--red-bright);
    display: flex;
    align-items: center;
    justify-content: center;
    text-align: center;
    font-family: "Lora", Georgia, serif;
    font-weight: 700;
    font-size: 17px;
    line-height: 1.35;
    color: var(--white);
  }
  .ad--banner .price-lock { left: 214px; }
  .ad--square .price-lock { left: 200px; }
</style>
</head>
<body>

  <section class="ad ad--banner">
    <div class="ad__photo" role="img" aria-label="Custom white board-and-batten home with a two-car black garage, stone base and landscaping"></div>
    <svg class="ad__edge" viewBox="0 0 605 504" aria-hidden="true">
      <polygon points="335,0 397,0 286,504 226,504" fill="var(--red-deep)"/>
      <polygon points="367,0 397,0 286,504 258,504" fill="var(--red)"/>
    </svg>
    <div class="brand">
      <span class="brand__mark"></span>
      <span class="brand__name">Hollis Bay</span>
    </div>
    <div class="badge" aria-label="CFRM member"></div>
    <h1 class="ad__title">FOREVER<br>HOME</h1>
    <p class="ad__copy">They are custom home builders in the mostly rural parts of West Virginia</p>
    <a class="ad__cta" href="#">LEARN MORE
      <svg viewBox="0 0 16 16"><circle cx="8" cy="8" r="8" fill="var(--white)"/><path d="M6.5 4.5 10 8l-3.5 3.5" stroke="var(--navy)" stroke-width="2" fill="none"/></svg>
    </a>
    <div class="price-lock">Price Lock<br>Available!</div>
  </section>

  <section class="ad ad--square">
    <div class="ad__photo" role="img" aria-label="Custom red board-and-batten home with white trim, grey roof and cupola, set against green trees"></div>
    <svg class="ad__edge" viewBox="0 0 504 504" aria-hidden="true">
      <polygon points="321,0 383,0 290,504 230,504" fill="var(--red-deep)"/>
      <polygon points="353,0 383,0 290,504 262,504" fill="var(--red)"/>
    </svg>
    <div class="brand">
      <span class="brand__mark"></span>
      <span class="brand__name">Hollis Bay</span>
    </div>
    <div class="badge" aria-label="CFRM member"></div>
    <h1 class="ad__title">FOREVER<br>HOME</h1>
    <p class="ad__copy">They are custom home builders in the mostly rural parts of West Virginia</p>
    <a class="ad__cta" href="#">LEARN MORE
      <svg viewBox="0 0 16 16"><circle cx="8" cy="8" r="8" fill="var(--white)"/><path d="M6.5 4.5 10 8l-3.5 3.5" stroke="var(--navy)" stroke-width="2" fill="none"/></svg>
    </a>
    <div class="price-lock">Price Lock<br>Available!</div>
  </section>

</body>
</html>
```